4D Cradle Glimpse Luxury Ultrasound Billboard

Design a HIGH-END, MODERN billboard for my private prenatal ultrasound studio, 4D Cradle Glimpse, located in Pace, Florida.
This billboard will be viewed by drivers traveling at highway speeds, so it must be extremely clean, simple, and readable within 6 seconds.
About My Business
4D Cradle Glimpse is a private prenatal ultrasound studio specializing in:
Highest technology 4D/HD Ultrasounds
Early Gender Determination
Pregnancy Confirmation
I have been serving families for nearly 10 years and is known for creating a memorable experience, not just an ultrasound appointment.
Design Style
I DO NOT want:
Flowers
Leaves
Swirls
Glitter
Hearts everywhere
Busy backgrounds
Generic maternity stock graphics
I DO want:
Modern
Luxury
Upscale
Clean
Professional
Eye-catching
Premium medical spa feel
Colors
Use colors from my logo:
LOGO Green ( or a deep green)
Black
White
Soft Gold accents
Images:
Incorporate my professional headshot in a clean, modern way, logo, and the ultrasound images
Text
Keep wording minimal.
Primary Headline ( OPEN TO IDEAS) :
EXAMPLES ( WOULD RATHER SOMETHING MORE CATCHY)
" ADVANCED IMAGING. UNFORGETTABLE MOMENTS"
"MEET YOUR BABY BEFORE BIRTH"
Under headline:
4D Ultrasound • Early Gender • Pregnancy Confirmation
Business Name:
4D Cradle Glimpse
Private Prenatal Ultrasound Studio
Phone Number:
850-471-5923
Important
This billboard must be readable in 5–6 seconds from a moving vehicle.
Less text is better.
The phone number and business name must be visible from a distance.
The design should feel like a premium brand that immediately tells expecting parents:
“This is where I go to see my baby.”
Files Provided
Official logo
Headshot
Ultrasound images
Don’t make this look like a medical office billboard.
Make it look like a luxury baby experience billboard. That’s what separates 4D Cradle Glimpse from hospitals, OB offices, and all the new studios popping up around you. The emotional connection is what gets moms to book. ❤️
Billboard Size - 10.6” x 36”

```html
<!DOCTYPE html>
<html lang="en">
<head>
<meta charset="utf-8">
<title>4D Cradle Glimpse Billboard</title>
<link href="https://fonts.googleapis.com/css2?family=Montserrat:wght@400;700&family=Open+Sans:wght@600;700&display=swap" rel="stylesheet">
<style>
  :root {
    --board-green: #263029;
    --page-bg: #e9ebea;
    --gold: #d9b144;
    --white: #ffffff;
    --photo-green: #3f5a45;
    --photo-light: #8d9a92;
    --scan-warm: #a8554a;
    --scan-deep: #5e2a25;
  }
  html, body {
    margin: 0;
    width: 1200px;
    height: 800px;
    overflow: hidden;
    background: var(--page-bg);
  }
  .billboard {
    position: absolute;
    left: 40px;
    top: 235px;
    width: 1120px;
    height: 330px;
    background: var(--board-green);
    overflow: hidden;
    font-family: "Open Sans", Arial, sans-serif;
    color: var(--white);
  }
  .brand {
    position: absolute;
    left: 15px;
    top: 80px;
    width: 280px;
    text-align: center;
  }
  .brand-name {
    font-family: "Montserrat", Arial, sans-serif;
    font-weight: 700;
    font-size: 27px;
    line-height: 1.1;
    color: var(--gold);
    margin: 0;
    white-space: nowrap;
  }
  .brand-tagline {
    margin: 14px 0 0;
    font-size: 13px;
    font-weight: 600;
    letter-spacing: 0.5px;
    white-space: nowrap;
  }
  .contact {
    position: absolute;
    left: 15px;
    top: 215px;
    width: 280px;
    text-align: center;
  }
  .contact-label {
    margin: 0;
    font-size: 15px;
    font-weight: 600;
  }
  .contact-phone {
    margin: 4px 0 0;
    font-size: 36px;
    font-weight: 700;
    color: var(--gold);
    letter-spacing: 0.5px;
    white-space: nowrap;
  }
  .portrait {
    position: absolute;
    left: 305px;
    top: 0;
    width: 235px;
    height: 330px;
    background: linear-gradient(160deg, var(--photo-light) 0%, var(--photo-green) 55%, #2c3d31 100%);
  }
  .scan {
    position: absolute;
    left: 495px;
    top: 148px;
    width: 148px;
    height: 148px;
    border: 5px solid var(--white);
    border-radius: 26px;
    background: radial-gradient(circle at 40% 45%, var(--scan-warm) 0%, var(--scan-deep) 100%);
  }
  .headline {
    position: absolute;
    left: 680px;
    top: 26px;
    margin: 0;
    font-family: "Montserrat", Arial, sans-serif;
    font-weight: 400;
    font-size: 52px;
    line-height: 60px;
    letter-spacing: -0.5px;
    text-transform: uppercase;
    white-space: nowrap;
  }
  .headline .accent {
    font-weight: 700;
    color: var(--gold);
  }
  .services {
    position: absolute;
    left: 680px;
    top: 232px;
    margin: 0;
    padding: 0;
    list-style: none;
    font-size: 18px;
    font-weight: 600;
    line-height: 26px;
  }
  .services li::before {
    content: "•";
    color: var(--gold);
    margin-right: 6px;
  }
</style>
</head>
<body>
  <section class="billboard">
    <div class="brand">
      <p class="brand-name">4D Cradle Glimpse</p>
      <p class="brand-tagline">PRENATAL ULTRASOUND STUDIO</p>
    </div>
    <div class="contact">
      <p class="contact-label">Phone:</p>
      <p class="contact-phone">850-471-5923</p>
    </div>
    <div class="portrait" role="img" aria-label="Headshot of the studio sonographer in green scrubs beside ultrasound equipment"></div>
    <div class="scan" role="img" aria-label="4D ultrasound image of twin babies"></div>
    <h1 class="headline">Meet your<br><span class="accent">Baby</span> before<br>Birth</h1>
    <ul class="services">
      <li>4D Ultrasound</li>
      <li>Early Gender</li>
      <li>Pregnancy Confirmation</li>
    </ul>
  </section>
</body>
</html>
```